Cocktail-Making Assistant App re-design

Ok boys and girls, here's the deal:
I have an android app which is almost complete, but needs a design overhaul.

The app is a standard cocktail-making assistant: gives you a list of cocktails and the ability to see which cocktail you can make out of those ingredients (drinks, fruit, etc) you have at home.

I've attached some general app flow, as well as detailed requirements/explanation presentation. Most of those things are just FYI, so that you know what it's about.

3 screens are the most important (main screen, cocktail view screen, ingredient view screen), meaning I will pick the design mostly based on ideas for those 3 things, with the fourth being a rather simple list (given on attached flow, third tier)
Some other screens are derived from that, with some minor changes on it, but you shouldn't care about that.

There are lots of other, non-explained things which I said nothing about only because they are (from design point of view) completely the same and would only make it seem more complicated.

I don't want to influence the colour scheme, but the app will be released under RedFig developer name (having a light colured red fig as a logo) so I suppose some brownish design, for example, will not really fit nicely. If you, however, have a killer which you are confident will prove me wrong, I'm looking forward to seeing it!

It should be a serious, elegant look (as opposed to cartoonish, but we are not aiming for a business look at all!), not cluttered with details, no clubbing themes, glitter and so on.

Test apk file available on request (Android 2.3+).

Edit: payment is now guaranteed
Also please note that currently, the favorite, "heart" button has a motion effect:
on click it flies out of the screen to the left (white heart) and comes back to the screen as a red heart. Take that into consideration, if it means anything to you.

Target Market(s)

Whoever you imagine would enjoy drinking cocktails

Industry/Entity Type

Business

Requirements
Must have
• Everything is said in the provided documentation - images say more than I could possibly write here.
Nice to have
• As said, most of the icons are a nice-to-have. Only those which are critically linked to the rest of the design must be provided. More details in the docs.
Should not have
• No cartoon look, No zillion colours

```html
<!DOCTYPE html>
<html lang="en">
<head>
<meta charset="utf-8">
<title>Cocktail Search – light and dark screens</title>
<link rel="stylesheet" href="https://fonts.googleapis.com/css2?family=Didact+Gothic&family=Nunito:wght@300;400&display=swap">
<style>
  :root {
    --page: #ffffff;
    --header-top: #0f6fbf;
    --header-bottom: #2aa6e6;
    --header-text: #ffffff;
    --light-bg-center: #ffffff;
    --light-bg-edge: #e3ecf6;
    --light-text: #1d1d1f;
    --light-line: #8a8c8f;
    --light-placeholder: #7d7f82;
    --light-nav: #e1e5ea;
    --light-nav-ring: #d3d8de;
    --light-nav-icon: #6d6f72;
    --dark-bg-top: #1d3c5e;
    --dark-bg-bottom: #231f20;
    --dark-text: #ffffff;
    --dark-line: #8d9095;
    --dark-button: #3e3a3b;
    --okay-bg: #d2d2d4;
    --okay-text: #ffffff;
  }
  * { box-sizing: border-box; margin: 0; padding: 0; }
  html, body { width: 1200px; height: 1024px; overflow: hidden; background: var(--page); }
  body { position: relative; font-family: "Didact Gothic", "Nunito", sans-serif; }

  .screen { position: absolute; top: 14px; width: 564px; height: 995px; overflow: hidden; }
  .screen--light { left: 14px; background: radial-gradient(ellipse at 40% 38%, var(--light-bg-center) 0%, var(--light-bg-edge) 75%); color: var(--light-text); }
  .screen--dark { left: 620px; background: linear-gradient(180deg, var(--dark-bg-top) 0%, var(--dark-bg-bottom) 42%); color: var(--dark-text); }

  .app-header { height: 94px; background: linear-gradient(180deg, var(--header-top), var(--header-bottom)); display: flex; align-items: center; justify-content: center; }
  .app-title { color: var(--header-text); font-weight: 400; font-size: 51px; letter-spacing: 0.5px; }

  .search-label { position: absolute; left: 40px; top: 152px; font-size: 30px; font-weight: 400; }
  .search-field { position: absolute; left: 62px; top: 208px; width: 450px; height: 51px; border: 3px solid var(--light-line); display: flex; align-items: center; padding: 0 16px; justify-content: space-between; }
  .screen--dark .search-field { border-color: var(--dark-line); }
  .search-placeholder { font-family: "Nunito", sans-serif; font-weight: 300; font-size: 19px; color: var(--light-placeholder); }
  .screen--dark .search-placeholder { color: #c9cbce; }
  .search-icon { width: 38px; height: 38px; }

  .search-hint { position: absolute; left: 82px; width: 400px; top: 280px; text-align: center; font-family: "Nunito", sans-serif; font-size: 17.5px; line-height: 26px; }

  .category-list { position: absolute; left: 52px; top: 482px; width: 449px; list-style: none; }
  .screen--dark .category-list { left: 50px; }
  .category { height: 74px; margin-bottom: 23px; display: flex; align-items: center; border: 3px solid var(--light-line); }
  .screen--dark .category { border: none; background: var(--dark-button); }
  .category-star { width: 48px; height: 48px; margin-left: 16px; }
  .category-name { margin-left: 92px; font-size: 42px; }

  .bottom-nav { position: absolute; left: 0; top: 880px; width: 564px; height: 100px; }
  .nav-track { position: absolute; left: 126px; top: 34px; width: 321px; height: 34px; background: var(--light-nav); }
  .nav-button { position: absolute; border-radius: 50%; background: var(--light-nav); border: 4px solid var(--light-nav-ring); display: flex; align-items: center; justify-content: center; }
  .nav-button--back { left: 97px; top: 22px; width: 58px; height: 58px; }
  .nav-button--home { left: 251px; top: 12px; width: 78px; height: 78px; }
  .nav-button--next { left: 418px; top: 22px; width: 58px; height: 58px; }
  .nav-icon { width: 36px; height: 36px; }
  .nav-button--home .nav-icon { width: 50px; height: 50px; }

  .dark-nav-icon { position: absolute; }
  .dark-nav-icon--back { left: 62px; top: 28px; width: 52px; height: 46px; }
  .dark-nav-icon--home { left: 200px; top: 20px; width: 60px; height: 56px; }
  .okay-button { position: absolute; left: 358px; top: 23px; width: 175px; height: 50px; background: var(--okay-bg); color: var(--okay-text); font-size: 28px; display: flex; align-items: center; justify-content: center; }
</style>
</head>
<body>
  <svg width="0" height="0" style="position:absolute">
    <defs>
      <symbol id="icon-star" viewBox="0 0 48 48"><polygon points="24,3 30,18 46,18.5 33.5,28.5 38,44 24,35 10,44 14.5,28.5 2,18.5 18,18"/></symbol>
      <symbol id="icon-home" viewBox="0 0 60 56"><polygon points="30,3 2,30 10,30 10,54 25,54 25,38 35,38 35,54 50,54 50,30 58,30"/></symbol>
      <symbol id="icon-arrow-left" viewBox="0 0 52 46"><polygon points="2,23 24,2 30,8 18,19 50,19 50,27 18,27 30,38 24,44"/></symbol>
      <symbol id="icon-arrow-right" viewBox="0 0 52 46"><polygon points="50,23 28,2 22,8 34,19 2,19 2,27 34,27 22,38 28,44"/></symbol>
    </defs>
  </svg>

  <section class="screen screen--light">
    <header class="app-header"><h1 class="app-title">Cocktail Search</h1></header>
    <h2 class="search-label">Search</h2>
    <div class="search-field">
      <span class="search-placeholder">Tap here to edit text &nbsp;. . .</span>
      <svg class="search-icon" viewBox="0 0 38 38"><circle cx="15" cy="15" r="10" fill="none" stroke="#eef1f4" stroke-width="4"/><line x1="22" y1="22" x2="34" y2="34" stroke="#eef1f4" stroke-width="6" stroke-linecap="round"/></svg>
    </div>
    <p class="search-hint">You can search the entire collection of all categories or else simply select a subcategory from below list.</p>
    <ul class="category-list">
      <li class="category"><svg class="category-star" fill="#231f20"><use href="#icon-star"/></svg><span class="category-name">All</span></li>
      <li class="category"><svg class="category-star" fill="#231f20"><use href="#icon-star"/></svg><span class="category-name">Cocktails</span></li>
      <li class="category"><svg class="category-star" fill="#231f20"><use href="#icon-star"/></svg><span class="category-name">Party Drinks</span></li>
    </ul>
    <nav class="bottom-nav">
      <div class="nav-track"></div>
      <div class="nav-button nav-button--back"><svg class="nav-icon" fill="var(--light-nav-icon)"><use href="#icon-arrow-left"/></svg></div>
      <div class="nav-button nav-button--home"><svg class="nav-icon" fill="var(--light-nav-icon)"><use href="#icon-home"/></svg></div>
      <div class="nav-button nav-button--next"><svg class="nav-icon" fill="var(--light-nav-icon)"><use href="#icon-arrow-right"/></svg></div>
    </nav>
  </section>

  <section class="screen screen--dark">
    <header class="app-header"><h1 class="app-title">Cocktail Search</h1></header>
    <h2 class="search-label">Search</h2>
    <div class="search-field">
      <span class="search-placeholder">Tap here to edit text &nbsp;. . .</span>
      <svg class="search-icon" viewBox="0 0 38 38"><circle cx="15" cy="15" r="10" fill="none" stroke="#ffffff" stroke-width="4"/><line x1="22" y1="22" x2="34" y2="34" stroke="#ffffff" stroke-width="6" stroke-linecap="round"/></svg>
    </div>
    <p class="search-hint">You can search the entire collection of all categories or else simply select a subcategory from below list.</p>
    <ul class="category-list">
      <li class="category"><svg class="category-star" fill="#ffffff"><use href="#icon-star"/></svg><span class="category-name">All</span></li>
      <li class="category"><svg class="category-star" fill="#ffffff"><use href="#icon-star"/></svg><span class="category-name">Cocktails</span></li>
      <li class="category"><svg class="category-star" fill="#ffffff"><use href="#icon-star"/></svg><span class="category-name">Party Drinks</span></li>
    </ul>
    <nav class="bottom-nav">
      <svg class="dark-nav-icon dark-nav-icon--back" fill="#ffffff"><use href="#icon-arrow-left"/></svg>
      <svg class="dark-nav-icon dark-nav-icon--home" fill="#ffffff"><use href="#icon-home"/></svg>
      <div class="okay-button">Okay !</div>
    </nav>
  </section>
</body>
</html>
```